tallow-brook.com

We are a small dollar lending company that will revolutionize the industry. We will do this by being completely transparent, fee free, etc and an interest rate that normal people can afford to pay. Over 10X less than our competition. We only allow our members to pay bills " bills paid fast", within 72 hours. Payday loans typically charge from 390%-600% with a terrible payback structure. We charge 36%, period, with a payback structure over 12 months. Our site will be very simple and easy to use but elegant at the same time. We do not want the site to be too busy, less is more and easier. We will have; Home, The Story, Why tallowbrook.com, Are you eligible? Members, Clients. To become a member you have to be referred by a current client of tallowbrook.com. A lot of the busy stuff will be saved for the Members and Clients sections. The feel must be elegant, easy to use and very simple to understand. I am looking for the green, white and black combinations of colors, very similar to my logo that was designed by Fernquillo.

```html
<!DOCTYPE html>
<html lang="en">
<head>
<meta charset="utf-8">
<title>tallow-brook.com</title>
<link href="https://fonts.googleapis.com/css2?family=Open+Sans:wght@300;400;600;700&family=Lato:wght@300;400&display=swap" rel="stylesheet">
<style>
:root{
  --green:#8dc63f;
  --green-light:#a3d75a;
  --green-dark:#7ab32f;
  --cream:#f4efe3;
  --ink:#2b2b2b;
  --grey:#8c8a86;
  --footer:#383838;
  --white:#ffffff;
}
*{margin:0;padding:0;box-sizing:border-box}
html,body{width:939px;height:1200px;overflow:hidden}
body{position:relative;background:var(--cream);font-family:'Open Sans',sans-serif;color:var(--grey)}
.abs{position:absolute}
.top-band{left:0;top:0;width:939px;height:355px;background:var(--green)}
.brand{left:98px;top:44px;display:flex;align-items:center;gap:8px;color:var(--white);font-size:21px;font-weight:400;letter-spacing:-.3px}
.brand-dot{width:30px;height:30px;border:3px solid var(--white);border-radius:50%}
.nav{left:340px;top:44px;height:40px;display:flex;border:1px solid rgba(255,255,255,.55);background:linear-gradient(#96cc4a,#84bd37)}
.nav a{display:flex;align-items:center;justify-content:center;height:100%;font-size:11px;font-weight:600;color:#3d5a16;text-decoration:none;white-space:nowrap;border-left:1px solid rgba(255,255,255,.45)}
.nav a:first-child{border-left:none;color:var(--white)}
.slider{left:86px;top:113px;width:767px;height:326px;background:var(--white);padding:4px 4px 4px 6px;box-shadow:0 14px 12px -10px rgba(0,0,0,.35)}
.slide-photo{width:100%;height:100%;background:linear-gradient(100deg,#a9c2a4 0%,#6f9673 35%,#9ea5a0 55%,#d4d6d4 75%,#8b8f8c 100%)}
.caption{left:91px;top:247px;width:402px;height:59px;background:rgba(60,60,60,.72);color:var(--white);font-size:19px;font-weight:400;white-space:nowrap;display:flex;align-items:center;padding-left:32px}
.dots{left:434px;top:423px;width:71px;height:24px;background:linear-gradient(#fbfbfb,#e2e2e2);border-radius:0 0 4px 4px;display:flex;justify-content:center;align-items:center;gap:8px}
.dots span{width:11px;height:11px;border-radius:50%;background:#c9c9c9;border:1px solid #9a9a9a}
.welcome-title{left:86px;top:474px;font-family:'Lato',sans-serif;font-weight:400;font-size:18.5px;color:var(--ink)}
.welcome-photo{left:86px;top:515px;width:204px;height:145px;border:4px solid var(--white);background:linear-gradient(#c9cbd6,#c7bca0 50%,#8b826a);box-shadow:0 0 2px rgba(0,0,0,.2)}
.copy{font-family:'Lato',sans-serif;font-weight:400;font-size:12.3px;line-height:19.6px;color:var(--grey);white-space:nowrap}
.welcome-text{left:304px;top:512px}
.welcome-more{left:86px;top:671px}
.btn{left:86px;top:723px;width:90px;height:37px;background:linear-gradient(var(--green-light),var(--green-dark));border:2px solid #bfe58f;color:var(--white);font-family:'Lato',sans-serif;font-size:13px;display:flex;align-items:center;justify-content:center}
.video{left:585px;top:515px;width:267px;height:203px;background:#111}
.video-still{width:100%;height:175px;background:linear-gradient(120deg,#c9a46a,#8a6a35 50%,#d8c49a)}
.video-bar{height:28px;display:flex;align-items:center;padding:0 8px;gap:8px;font-size:7.5px;color:var(--white);font-weight:700}
.video-bar .track{width:60px;height:3px;background:#444}
.video-bar .red{color:#e02020}
.play-ring{left:122px;top:68px;width:30px;height:30px}
.mid-band{left:0;top:795px;width:939px;height:284px;background:radial-gradient(ellipse at 50% 40%,#a6db62,var(--green) 60%)}
.col-title{font-size:15px;font-weight:600;color:var(--ink)}
.col-photo{width:245px;height:97px;border:3px solid #e7f0dc}
.col-text{font-family:'Open Sans',sans-serif;font-weight:400;font-size:11px;letter-spacing:-.25px;line-height:19.6px;color:#3d5a16;white-space:nowrap}
.more-link{font-size:11.5px;color:var(--white)}
.thumb{left:608px;width:57px;height:52px;border:2px solid #e7f0dc}
.news-title{left:678px;font-size:12px;font-weight:600;color:var(--white);white-space:nowrap}
.news-date{left:678px;font-size:9.5px;color:var(--white)}
.footer{left:0;top:1079px;width:939px;height:121px;background:var(--footer)}
.foot-nav{left:0;top:1097px;width:939px;display:flex;justify-content:center;gap:28px;font-size:10px;color:var(--white);font-weight:600}
.social{left:410px;top:1126px;display:flex;gap:1px}
.social span{width:30px;height:30px;border-radius:50%;background:var(--white)}
.copyright{left:0;top:1170px;width:939px;text-align:center;font-size:9.5px;color:var(--white)}
</style>
</head>
<body>
<div class="abs top-band"></div>

<div class="abs brand"><span class="brand-dot"></span>tallow-brook</div>

<nav class="abs nav">
  <a style="width:60px">HOME</a>
  <a style="width:84px">THE STORY</a>
  <a style="width:162px">WHY TALLOWBROOK.COM</a>
  <a style="width:136px">ARE YOU ELIGIBLE?</a>
  <a style="width:70px">CLIENTS</a>
</nav>

<div class="abs slider"><div class="slide-photo" role="img" aria-label="Close-up of a banknote engraving beside a silver coin"></div></div>
<div class="abs caption">We are a small dollar lending company</div>
<div class="abs dots"><span></span><span></span><span></span></div>

<h1 class="abs welcome-title">Welcome tallow-brook</h1>
<div class="abs welcome-photo" role="img" aria-label="Stack of dollar bills in front of a bar chart"></div>
<p class="abs copy welcome-text">Lorem ipsum dolor sit amet, consectetur<br>adipisicing elit, sed do eiusmod tempor<br>incididunt ut labore et dolore magna aliqua.<br>Ut enim ad minim veniam, quis nostrud ex-<br>ercitation ullamco laboris nisi ut aliquip ex<br>ea commodo consequat. Duis aute irure<br>dolor in reprehenderit in voluptate velit<br>esse cillum dolore eu fugiat nulla pariatur.</p>
<p class="abs copy welcome-more">Lorem ipsum dolor sit amet, consectetur adipisicing elit, sed do eiusmod tempor<br>incididunt ut labore et dolore magna aliqua. Ut enim ad minim veniam, quis nostrud</p>
<div class="abs btn">Read More</div>

<div class="abs video">
  <div class="video-still" role="img" aria-label="Old key lying on a pile of dollar bills"></div>
  <div class="video-bar">
    <svg width="14" height="14" viewBox="0 0 14 14"><circle cx="7" cy="7" r="7" fill="#555"/><path d="M5 4l5 3-5 3z" fill="#fff"/></svg>
    <span class="track"></span>
    <span>00:00 / <span class="red">00:00</span></span>
    <svg width="60" height="10" viewBox="0 0 60 10"><path d="M0 3h3l4-3v10l-4-3H0z" fill="#bbb"/><circle cx="30" cy="5" r="3" fill="#fff"/><rect x="50" y="1" width="8" height="8" fill="none" stroke="#bbb"/></svg>
  </div>
  <svg class="abs play-ring" viewBox="0 0 30 30"><circle cx="15" cy="15" r="13.5" fill="none" stroke="#fff" stroke-width="1.5"/><path d="M13 9l6 6-6 6" fill="none" stroke="#fff" stroke-width="1.5"/></svg>
</div>

<div class="abs mid-band"></div>

<h2 class="abs col-title" style="left:86px;top:816px">Organize</h2>
<div class="abs col-photo" style="left:86px;top:855px;background:linear-gradient(90deg,#c98a78,#a87060 40%,#c9cfc4)" role="img" aria-label="Hand counting a stack of banknotes"></div>
<p class="abs col-text" style="left:86px;top:972px">Lorem ipsum dolor sit amet, consectetur<br>adipisicing elit, sed do eiusmod tempor incid-<br>idunt ut labore et dolore magna aliqua</p>
<div class="abs more-link" style="left:86px;top:1050px">READ MORE...</div>

<h2 class="abs col-title" style="left:347px;top:816px">Dollar lending</h2>
<div class="abs col-photo" style="left:347px;top:855px;background:linear-gradient(90deg,#b8bdaa,#7f8771 50%,#c4c8b8)" role="img" aria-label="Scattered twenty dollar bills"></div>
<p class="abs col-text" style="left:347px;top:972px">Lorem ipsum dolor sit amet, consectetur<br>adipisicing elit, sed do eiusmod tempor incid-<br>idunt ut labore et dolore magna aliqua</p>
<div class="abs more-link" style="left:347px;top:1050px">READ MORE...</div>

<h2 class="abs col-title" style="left:608px;top:816px">Recent News</h2>
<div class="abs thumb" style="top:853px;background:linear-gradient(#b66a3a,#7d3f1c)" role="img" aria-label="Stacked copper coins"></div>
<div class="abs news-title" style="top:849px">Lorem ipsum dolor sit amet</div>
<div class="abs news-date" style="top:872px">April07 &nbsp;2014</div>
<div class="abs thumb" style="top:914px;background:linear-gradient(#d8d3c4,#b8ad95)" role="img" aria-label="Financial statement page"></div>
<div class="abs news-title" style="top:910px">Lorem ipsum dolor sit amet</div>
<div class="abs news-date" style="top:931px">April07 &nbsp;2014</div>
<div class="abs thumb" style="top:984px;background:linear-gradient(#c8ccd8,#6f7486)" role="img" aria-label="Rolled banknote"></div>
<div class="abs news-title" style="top:980px">Lorem ipsum dolor sit amet</div>
<div class="abs news-date" style="top:1003px">April07 &nbsp;2014</div>
<div class="abs more-link" style="left:608px;top:1050px">VIEW MORE</div>

<footer class="abs footer"></footer>
<div class="abs foot-nav"><span>Home</span><span>The Story</span><span>Why tallowbrook.com</span><span>Are you eligible?</span><span>Clients</span></div>
<div class="abs social"><span></span><span></span><span></span><span></span></div>
<div class="abs copyright">Copyright © 2014 tallow-brook.com. All rights reserved.</div>
</body>
</html>
```